New Business Card Design Project

I need a design for business cards, i am an electrical business called "Corvane Electrical and Communications" i need the cards to be double sided with the company logo on the back (attached) the front needs to say my company name, web site, email address, telephone number, and ABN number and electrical license number. I am open to different arrangements of the information but would like the background to be incorporating something electrical or something that looks smart. open to all additional ideas also.

The company colours are orange and grey see logo attached.

Business Name: Corvane Electrical and Communications
Website: corvaneelectricalandcomms.example.com.au
Email: brent@corvaneelectricalandcomms.example.com.au
Telephone(mobile): 0481209736
ABN: 71208349162
Lic No: 418273D

Target Market(s)

Business entities, Project Managers, Accounts, Clients

Industry/Entity Type

Electrician

Contact Information for Business Card

I need a design for business cards, i am an electrical business called "Corvane Electrical and Communications" i need the cards to be double sided with the company logo on the back (attached) the front needs to say my company name

Font styles to use
Serif
Sans Serif

Colors
f37122
5c5c5c

Requirements
Must have
• Must have the Logo on the back open to different ways of it being on the back but had in mind to keep it central but again open to other options
Nice to have
• A real modern cool background that is eye catching yet contemporary
Should not have
• No backgrounds of a light bulb or plug or anything like that

```html
<!DOCTYPE html>
<html lang="en">
<head>
<meta charset="utf-8">
<title>Corvane Electrical and Communications – Business Cards</title>
<link rel="stylesheet" href="https://fonts.googleapis.com/css2?family=Open+Sans:wght@400;600&display=swap">
<style>
  :root {
    --stage: #3b3532;
    --card: #141414;
    --orange: #f3a322;
    --white: #f2f2f2;
    --grey: #5c5c5c;
    --divider: #4a4a4a;
  }
  * { margin: 0; padding: 0; box-sizing: border-box; }
  html, body {
    width: 1200px; height: 814px; overflow: hidden;
    background: var(--stage);
    font-family: "Open Sans", Arial, sans-serif;
  }
  .canvas {
    position: relative; width: 1200px; height: 814px;
    display: flex; align-items: center; justify-content: center; gap: 30px;
  }
  .card {
    position: relative; width: 560px; height: 320px;
    background: var(--card);
    border-radius: 3px;
    box-shadow: 0 10px 30px rgba(0,0,0,.45);
  }
  /* front */
  .brand {
    position: absolute; left: 28px; top: 150px; width: 180px;
    font-weight: 600; font-size: 34px; letter-spacing: 1px;
    color: var(--white); text-transform: uppercase;
    display: flex; align-items: center; gap: 8px;
  }
  .brand-dot {
    width: 12px; height: 12px; border-radius: 50%; background: var(--orange); flex: none;
  }
  .brand-sub {
    position: absolute; left: 28px; top: 198px; width: 180px;
    font-weight: 600; font-size: 8.5px; letter-spacing: .6px;
    color: var(--orange); text-transform: uppercase;
  }
  .divider {
    position: absolute; left: 222px; top: 92px; width: 1px; height: 150px;
    background: var(--divider);
  }
  .details {
    position: absolute; left: 240px; top: 92px; width: 300px;
    color: var(--white); font-size: 11.5px; line-height: 17px;
  }
  .person-name { color: var(--orange); font-weight: 600; font-size: 15px; line-height: 20px; }
  .contact-row { display: flex; align-items: center; gap: 6px; }
  .contact-row svg { width: 13px; height: 13px; flex: none; }
  .contact-list { margin-top: 2px; }
  /* back */
  .back-brand {
    position: absolute; left: 0; right: 0; top: 118px; text-align: center;
    font-weight: 600; font-size: 40px; letter-spacing: 2px;
    color: var(--orange); text-transform: uppercase;
  }
  .back-url {
    position: absolute; left: 0; right: 0; top: 206px; text-align: center;
    color: var(--white); font-size: 11px; letter-spacing: 1.2px;
  }
</style>
</head>
<body>
<main class="canvas">
  <section class="card card-front" aria-label="Card front">
    <div class="brand"><span class="brand-dot"></span>Corvane</div>
    <div class="brand-sub">Electrical &amp; Communications</div>
    <div class="divider"></div>
    <div class="details">
      <p class="person-name">Dale Merritt</p>
      <p>CEO/Founder</p>
      <p>ABN: 71208349162</p>
      <p>Lic No: 418273D</p>
      <div class="contact-list">
        <p class="contact-row">
          <svg viewBox="0 0 14 14" aria-hidden="true"><rect x="3.5" y="1" width="7" height="12" rx="1.2" fill="none" stroke="var(--orange)" stroke-width="1.4"/><circle cx="7" cy="11" r=".8" fill="var(--orange)"/></svg>
          0481209736
        </p>
        <p class="contact-row">
          <svg viewBox="0 0 14 14" aria-hidden="true"><rect x="1" y="3" width="12" height="8" fill="var(--orange)"/><path d="M1 3l6 4.5L13 3" fill="none" stroke="var(--card)" stroke-width="1"/></svg>
          brent@corvaneelectricalandcomms.example.com.au
        </p>
        <p class="contact-row">
          <svg viewBox="0 0 14 14" aria-hidden="true"><circle cx="7" cy="7" r="6" fill="var(--orange)"/><path d="M1 7h12M7 1c-2.5 3-2.5 9 0 12M7 1c2.5 3 2.5 9 0 12" fill="none" stroke="var(--card)" stroke-width=".9"/></svg>
          corvaneelectricalandcomms.example.com.au
        </p>
      </div>
    </div>
  </section>
  <section class="card card-back" aria-label="Card back">
    <div class="back-brand">Corvane</div>
    <p class="back-url">www.corvaneelectricalandcomms.example.com.au</p>
  </section>
</main>
</body>
</html>
```